MRT Property - Business Cards

Looking for a business card & general letterhead, signage etc design for our new logo.

Colours:
000a20
0056a2
00b5ef
0088ce
68cef2

Fonts:
Poppins
Karla

Please keep look and feel of new brand - example in the zip package I sent.

```html
<!DOCTYPE html>
<html lang="en">
<head>
<meta charset="utf-8">
<title>MRT Property – Business Cards</title>
<link rel="stylesheet" href="https://fonts.googleapis.com/css2?family=Montserrat:wght@400;700&family=Julee&display=swap">
<style>
  :root {
    --backdrop: #9a9a9a;
    --card: #121527;
    --navy: #000a20;
    --brand-blue: #0056a2;
    --mid-blue: #0088ce;
    --bright-blue: #00b5ef;
    --light-blue: #68cef2;
    --pattern-blue: #3f55a0;
    --text-light: #e6eaf2;
    --white: #ffffff;
  }
  * { box-sizing: border-box; margin: 0; padding: 0; }
  html, body {
    width: 1093px; height: 1200px; overflow: hidden;
    background: var(--backdrop);
    font-family: "Montserrat", Arial, sans-serif;
  }
  .card {
    position: absolute; left: 265px; width: 580px; height: 362px;
    background: var(--card); border-radius: 20px; overflow: hidden;
  }
  .card--front { top: 225px; }
  .card--back { top: 616px; height: 366px; }

  .brand-sweep {
    position: absolute; left: 0; top: 0; width: 290px; height: 100%;
    background: linear-gradient(100deg, var(--light-blue) 0%, var(--mid-blue) 40%, var(--card) 100%);
  }
  .front-info { position: absolute; left: 303px; top: 0; right: 20px; color: var(--text-light); }
  .wordmark {
    position: absolute; top: 56px; white-space: nowrap;
    font-weight: 700; font-size: 29px; color: var(--brand-blue); letter-spacing: 0.5px;
  }
  .person-name {
    position: absolute; top: 148px; white-space: nowrap;
    font-family: "Julee", cursive; font-size: 27px; color: var(--brand-blue);
  }
  .person-title { position: absolute; top: 181px; font-size: 13px; white-space: nowrap; }
  .address { position: absolute; top: 217px; font-size: 13px; line-height: 16px; white-space: nowrap; }
  .contact { position: absolute; top: 270px; list-style: none; font-size: 13px; }
  .contact li { display: flex; align-items: center; height: 24.5px; white-space: nowrap; }
  .contact svg { width: 13px; height: 13px; margin-right: 8px; fill: var(--mid-blue); }

  .back-pattern {
    position: absolute; inset: 0;
    background: linear-gradient(145deg, var(--pattern-blue) 0%, #252a4a 30%, #14172a 55%, var(--card) 100%);
  }
  .back-brand {
    position: absolute; left: 352px; top: 272px;
    display: flex; align-items: center; gap: 8px;
  }
  .back-brand__dot { width: 30px; height: 30px; border-radius: 50%; background: var(--mid-blue); }
  .back-brand__name { font-weight: 700; font-size: 20px; color: var(--white); white-space: nowrap; }
</style>
</head>
<body>
  <section class="card card--front">
    <div class="brand-sweep" role="img" aria-label="Large brand symbol in light and mid blue sweeping curves"></div>
    <div class="front-info">
      <div class="wordmark">MRT Property</div>
      <div class="person-name">Daniel Carter</div>
      <div class="person-title">Managing Director</div>
      <div class="address">240 Harbor Crest Lane<br>Ridgeview, TX 75001</div>
      <ul class="contact">
        <li><svg viewBox="0 0 24 24"><path d="M6.6 10.8a15.1 15.1 0 0 0 6.6 6.6l2.2-2.2a1 1 0 0 1 1-.25 11.4 11.4 0 0 0 3.6.57 1 1 0 0 1 1 1V20a1 1 0 0 1-1 1A17 17 0 0 1 3 4a1 1 0 0 1 1-1h3.5a1 1 0 0 1 1 1c0 1.25.2 2.45.57 3.57a1 1 0 0 1-.25 1z"/></svg>555.014.2290</li>
        <li><svg viewBox="0 0 24 24"><path d="M2 5h20v2l-10 6L2 7z M2 9l10 6 10-6v10H2z"/></svg>info@mrtproperty.com</li>
        <li><svg viewBox="0 0 24 24"><circle cx="12" cy="12" r="10"/></svg>www.mrtproperty.com</li>
      </ul>
    </div>
  </section>

  <section class="card card--back">
    <div class="back-pattern" role="img" aria-label="Repeating brand symbol pattern fading from blue to dark navy"></div>
    <div class="back-brand">
      <span class="back-brand__dot"></span>
      <span class="back-brand__name">MRT Property</span>
    </div>
  </section>
</body>
</html>
```